BUSINESS CARD DESIGN

NAME- DALE VORSKIN
PHONE NUMER - 555- 714-9082
EMAIL- OFFICE@TRV-GROUNDMAKRZ.COM
BACK OF CARD- SPEACIALIZES IN LAND CLEARING, FORESTRY MUCLHING AND EXCAVATION

Contact Information for Business Card

NAME- DALE VORSKIN PHONE NUMER - 555- 714-9082 EMAIL- OFFICE@TRV-GROUNDMAKRZ.COM BACK OF CARD- SPEACIALIZES IN LAND CLEARING , MUCLHING AND EXCAVATION

```html
<!DOCTYPE html>
<html lang="en">
<head>
<meta charset="utf-8">
<title>Terravale Groundmakrz – Business Card</title>
<link href="https://fonts.googleapis.com/css2?family=Montserrat:wght@500;600;700&display=swap" rel="stylesheet">
<style>
  :root {
    --gold: #f7b217;
    --card-yellow: #f8b31a;
    --ink: #000000;
    --paper: #ffffff;
  }
  * { margin: 0; padding: 0; box-sizing: border-box; }
  html, body { width: 1200px; height: 1131px; overflow: hidden; background: var(--paper); }
  body { position: relative; font-family: "Montserrat", Arial, sans-serif; }

  .card { position: absolute; left: 229px; width: 689px; height: 394px; overflow: hidden; }
  .card--front { top: 151px; background: var(--ink); }
  .card--back { top: 626px; background: var(--card-yellow); }

  .front-panel { position: absolute; inset: 0; }

  .brand { position: absolute; display: flex; flex-direction: column; align-items: center; text-align: center; font-weight: 700; }
  .brand__mark { border-radius: 50%; }
  .brand__name { letter-spacing: 0.06em; line-height: 1.15; }
  .brand__phone { letter-spacing: 0.5em; }

  .card--front .brand { left: 46px; top: 112px; width: 200px; color: var(--gold); }
  .card--front .brand__mark { width: 80px; height: 80px; background: var(--gold); margin-bottom: 12px; }
  .card--front .brand__name { font-size: 16px; }
  .card--front .brand__phone { font-size: 9px; margin-top: 6px; }

  .card--back .brand { left: 204px; top: 70px; width: 280px; color: var(--ink); }
  .card--back .brand__mark { width: 110px; height: 110px; background: var(--ink); margin-bottom: 16px; }
  .card--back .brand__name { font-size: 22px; }
  .card--back .brand__phone { font-size: 11px; margin-top: 8px; }

  .person { position: absolute; left: 394px; top: 124px; color: var(--gold); font-weight: 600; }
  .person__name { font-size: 30px; line-height: 1; letter-spacing: 0.01em; }
  .person__role { display: inline-block; font-size: 22px; line-height: 1; margin-top: 8px; padding: 0 2px 4px 0; border-bottom: 3px solid var(--gold); width: 100px; }

  .contacts { position: absolute; left: 388px; top: 244px; list-style: none; color: var(--gold); font-weight: 700; font-size: 16px; }
  .contacts__item { display: flex; align-items: center; height: 24px; margin-bottom: 17px; }
  .contacts__icon { width: 30px; height: 24px; margin-right: 16px; flex: none; }

  .tagline { position: absolute; left: 0; right: 0; top: 353px; text-align: center; font-size: 14px; font-weight: 700; letter-spacing: 0.04em; color: var(--ink); }
</style>
</head>
<body>

<section class="card card--front" aria-label="Card front">
  <svg class="front-panel" width="689" height="394" viewBox="0 0 689 394" aria-hidden="true">
    <path d="M290,394 C290,180 460,20 663,0 L689,0 L689,394 Z" fill="#ffffff"/>
  </svg>

  <div class="brand">
    <span class="brand__mark"></span>
    <span class="brand__name">TERRAVALE<br>GROUNDMAKRZ LLC</span>
    <span class="brand__phone">555-714-9082</span>
  </div>

  <div class="person">
    <p class="person__name">DALE VORSKIN</p>
    <p class="person__role">OWNER</p>
  </div>

  <ul class="contacts">
    <li class="contacts__item">
      <svg class="contacts__icon" viewBox="0 0 30 24" aria-hidden="true">
        <rect x="1" y="4" width="28" height="16" fill="#f7b217"/>
        <path d="M1,4 L15,14 L29,4 M1,20 L12,11 M29,20 L18,11" stroke="#ffffff" stroke-width="2" fill="none"/>
      </svg>
      <span>@TRV-GROUNDMAKRZ.COM</span>
    </li>
    <li class="contacts__item">
      <svg class="contacts__icon" viewBox="0 0 30 24" aria-hidden="true">
        <path d="M6,2 L10,2 L12,8 L9,10 C11,14 13,16 17,18 L19,15 L25,17 L25,21 C25,22 24,23 22,23 C12,22 4,14 3,5 C3,3 4,2 6,2 Z" fill="none" stroke="#f7b217" stroke-width="1.6"/>
        <path d="M17,3 C21,3 24,6 24,10 M17,7 C19,7 20,8 20,10" fill="none" stroke="#f7b217" stroke-width="1.6"/>
      </svg>
      <span>+555- 714-9082</span>
    </li>
    <li class="contacts__item">
      <svg class="contacts__icon" viewBox="0 0 30 24" aria-hidden="true">
        <g fill="none" stroke="#f7b217" stroke-width="1.6">
          <circle cx="15" cy="12" r="11"/>
          <ellipse cx="15" cy="12" rx="5" ry="11"/>
          <path d="M4,12 L26,12 M6,6 L24,6 M6,18 L24,18"/>
        </g>
      </svg>
      <span>www.trv-groundmakrz.com</span>
    </li>
  </ul>
</section>

<section class="card card--back" aria-label="Card back">
  <div class="brand">
    <span class="brand__mark"></span>
    <span class="brand__name">TERRAVALE<br>GROUNDMAKRZ LLC</span>
    <span class="brand__phone">555-714-9082</span>
  </div>
  <p class="tagline">SPEACIALIZES IN LAND CLEARING , MUCLHING AND EXCAVATION</p>
</section>

</body>
</html>
```